Website redesign - vorelmik.com

We are looking to do a full redesign of vorelmik.com. Need a designer to come up overall layout and 3 specific pages and 3 different hero images.
Wireframes for the 3 pages are attached as well as site images. You don't have to follow the wireframes exactly, but instead the wireframe is there to show you the information that needs to be on each page. Feel free to rearrange as needed.
Our target market is self taught engineers. So definitely I want a more casual feel to it. I'm ok with fun bold colors as well. Really like websites that have the infinite scroll look/feel to them.
Looking to find a designer who will produce HTML and potentially even implement the HTML into our site checked in code.
HTML Code should be responsive/mobile first leveraging Bootstrap 4.
Attached files include:
0) Wireframe PDF
https://files.plomwerk.net/d/7Kx2pQmW9zLr4TbN8vYc3HsE5fJ/view?mode=share
1) Vorelmik Images zip 1
https://files.plomwerk.net/d/4Gt8nRvB2wQx6MkZ1pLd9YaC7hU/view?mode=share
2) Vorelmik Images zip 2
https://files.plomwerk.net/d/9Jw3sTcF5yNv1HqX8rKb2ZeM6dP/view?mode=share
Target Market(s)
I sell DIY Waterproof Electronics enclosures. Target audience is self taught DIY engineers
Coding
Coded - Design and coding required
Number of Pages Required
3 page
Colors
Designer to choose colors to be used in the design.
Look and feel

```html
<!DOCTYPE html>
<html lang="en">
<head>
<meta charset="utf-8">
<title>Vorelmik — Waterproof Project Boxes</title>
<link href="https://fonts.googleapis.com/css2?family=Rubik:wght@300;400;500&display=swap" rel="stylesheet">
<style>
:root{
  --ink:#2b2b2b;
  --muted:#555a63;
  --blue:#2020d8;
  --navy:#1d2331;
  --gold-1:#f0c419;
  --gold-2:#c99700;
  --mist:#e1e5ec;
  --tile:#f1f1f1;
  --footer:#222222;
  --white:#ffffff;
}
*{box-sizing:border-box;margin:0;padding:0}
html,body{width:1200px;height:4073px;overflow:hidden}
body{position:relative;font-family:"Rubik",sans-serif;font-weight:300;color:var(--ink);background:var(--white)}
.abs{position:absolute}
.btn{position:absolute;display:flex;align-items:center;justify-content:center;width:160px;height:47px;
  background:linear-gradient(180deg,var(--gold-1),var(--gold-2));color:#222;font-size:20px;font-weight:400;
  text-decoration:none;box-shadow:0 2px 3px rgba(0,0,0,.25)}
.site-header{position:absolute;left:0;top:0;width:1200px;height:52px;background:var(--white)}
.brand{position:absolute;left:144px;top:15px;font-size:18px;font-weight:500;color:var(--blue)}
.main-nav{position:absolute;left:570px;top:17px;display:flex;gap:24px;font-size:13px}
.main-nav a{color:var(--muted);text-decoration:none}
.main-nav a.active{color:var(--blue)}
.auth{position:absolute;top:12px;height:28px;border:1px solid #333;border-radius:3px;font-size:11px;
  display:flex;align-items:center;justify-content:center;text-decoration:none;color:#222}
.auth.signin{left:935px;width:56px}
.auth.signup{left:999px;width:56px;border-color:var(--blue);color:var(--blue)}
.band{position:absolute;left:0;width:1200px}
.arrow{position:absolute;width:26px;height:30px}
.photo{position:absolute}
.hero-title{position:absolute;color:var(--white);font-size:33px;line-height:40px;font-weight:300}
.hero-sub{position:absolute;color:var(--white);font-size:15px}
.section-title{position:absolute;color:var(--blue);font-size:32px;line-height:40px;font-weight:300}
.gold-frame{position:absolute;background:#d9a500}
.play{position:absolute;width:48px;height:48px;border-radius:50%;background:var(--white)}
.features{position:absolute;left:620px;top:1904px;list-style:none;font-size:19px;color:#333;line-height:29px}
.features li{position:absolute;left:0;width:460px;padding-left:16px;white-space:nowrap}
.features li::before{content:"";position:absolute;left:0;top:13px;width:5px;height:5px;border-radius:50%;background:#333}
.centered-title{position:absolute;left:0;width:1200px;text-align:center;color:var(--blue);font-size:32px;font-weight:300}
.review{position:absolute;top:2504px;width:444px;height:201px;background:var(--white)}
.avatar{position:absolute;top:-47px;left:24px;width:96px;height:96px;background:#a6adb8}
.reviewer{position:absolute;left:0;top:63px;width:144px;text-align:center;font-size:13px;color:#222;font-weight:400}
.reviewer small{display:block;font-size:9px;color:#777;font-weight:300;margin-top:3px}
.review p{position:absolute;left:150px;top:18px;width:290px;font-size:18px;line-height:29px;color:#333;white-space:nowrap}
.quote-mark{position:absolute;right:24px;bottom:-26px;font-size:90px;line-height:90px;color:#b5b8bd;font-family:Georgia,serif;height:50px}
.tile{position:absolute;width:297px;height:198px;background:var(--tile)}
.tile .shot{position:absolute;left:58px;top:30px;width:181px;height:118px;border-radius:4px}
.tile .label{position:absolute;left:16px;top:180px;width:266px;height:54px;background:linear-gradient(180deg,var(--gold-1),#e0ab00);
  display:flex;align-items:center;justify-content:center;font-size:14px;color:#222;font-weight:400}
.shot.dark{background:linear-gradient(160deg,#5a5d61,#2c2e31)}
.shot.green{background:linear-gradient(160deg,#6e7e5c,#33362f)}
.shot.steel{background:linear-gradient(160deg,#a4a7aa,#4a4c4f)}
.shot.tan{background:linear-gradient(160deg,#c29255,#8d6230)}
.view-all{position:absolute;left:539px;top:3785px;width:120px;height:46px;background:linear-gradient(180deg,#444,#1e1e1e);
  color:var(--white);display:flex;align-items:center;justify-content:center;font-size:20px;text-decoration:none}
.footer-links{position:absolute;left:144px;top:3990px;font-size:12px;color:#bbb;display:flex;gap:12px}
.footer-links a{color:#bbb;text-decoration:none}
.copyright{position:absolute;left:144px;top:4018px;font-size:11px;color:#aaa}
.follow{position:absolute;left:882px;top:4003px;font-size:16px;color:#bbb}
.social{position:absolute;top:3995px;width:36px;height:36px;border:1.5px solid #888;border-radius:50%}
</style>
</head>
<body>

<header class="site-header">
  <div class="brand">Vorelmik</div>
  <nav class="main-nav">
    <a class="active" href="#">Get Started</a><a href="#">Designs</a><a href="#">FAQs</a><a href="#">Videos</a><a href="#">Contact Us</a>
  </nav>
  <a class="auth signin" href="#">Sign In</a>
  <a class="auth signup" href="#">Sign Up</a>
</header>

<svg class="band" style="top:52px;height:561px" viewBox="0 0 1200 561" aria-hidden="true">
  <defs><linearGradient id="heroBg" x1="0" y1="0" x2="1" y2="1"><stop offset="0" stop-color="#252a33"/><stop offset="1" stop-color="#14171d"/></linearGradient></defs>
  <polygon points="0,0 1200,0 1200,561 0,522" fill="url(#heroBg)"/>
</svg>
<div class="photo" role="img" aria-label="Assembled electronics mounting kit with circuit boards and wiring" style="left:146px;top:125px;width:520px;height:390px;border-radius:10px;background:linear-gradient(150deg,#6f6d60 0%,#4d5a45 45%,#3b3a38 100%)"></div>
<svg class="arrow" style="left:54px;top:298px" viewBox="0 0 26 30"><path d="M18 3 L6 15 L18 27" stroke="#fff" stroke-width="6" fill="none"/></svg>
<svg class="arrow" style="left:1118px;top:298px" viewBox="0 0 26 30"><path d="M8 3 L20 15 L8 27" stroke="#fff" stroke-width="6" fill="none"/></svg>
<h1 class="hero-title" style="left:694px;top:206px;width:380px">Waterproof Project Boxes Customized to your Exact Needs.</h1>
<div class="hero-sub" style="left:694px;top:335px">(at a fraction of the price)</div>
<a class="btn" href="#" style="left:694px;top:370px">GET STARTED</a>

<div class="gold-frame" style="left:144px;top:703px;width:424px;height:312px"></div>
<div class="photo" role="img" aria-label="Video still of a grey and a black project box mounted outdoors" style="left:152px;top:694px;width:423px;height:313px;background:linear-gradient(135deg,#8b8d90 0%,#5a5148 50%,#3a2e24 100%)"></div>
<div class="play" style="left:336px;top:830px"></div>
<svg class="abs" style="left:352px;top:842px" width="20" height="24" viewBox="0 0 20 24"><path d="M2 1 L19 12 L2 23Z" fill="#111"/></svg>
<h2 class="section-title" style="left:666px;top:782px;width:420px">Customize your Project Box using our Designer</h2>
<a class="btn" href="#" style="left:667px;top:873px">GET STARTED</a>

<svg class="band" style="top:1092px;height:604px" viewBox="0 0 1200 604" aria-hidden="true">
  <polygon points="0,0 1200,42 1200,604 0,565" fill="var(--navy)"/>
</svg>
<svg class="arrow" style="left:54px;top:1400px" viewBox="0 0 26 30"><path d="M18 3 L6 15 L18 27" stroke="#fff" stroke-width="6" fill="none"/></svg>
<svg class="arrow" style="left:1118px;top:1400px" viewBox="0 0 26 30"><path d="M8 3 L20 15 L8 27" stroke="#fff" stroke-width="6" fill="none"/></svg>
<h2 class="hero-title" style="left:144px;top:1300px;width:420px">Mounting Kits for all the popular water proof project boxes with many sizes to choose from</h2>
<a class="btn" href="#" style="left:144px;top:1475px">GET STARTED</a>
<div class="photo" role="img" aria-label="Light grey hinged waterproof enclosure" style="left:620px;top:1238px;width:435px;height:354px;border-radius:20px;background:linear-gradient(160deg,#e4e4e2,#bdbdba)"></div>

<div class="gold-frame" style="left:144px;top:1784px;width:424px;height:416px"></div>
<div class="photo" role="img" aria-label="Mounting plate laid out with boards, power supply and screws" style="left:152px;top:1775px;width:423px;height:419px;background:linear-gradient(135deg,#8a6b4a,#a98a66 50%,#6d5238)"></div>
<h2 class="section-title" style="left:620px;top:1768px;width:470px">Vorelmik waterproof project boxes were built by makers for makers</h2>
<ul class="features">
  <li style="top:0">Design to your specifications</li>
  <li style="top:58px">Maker components: Quarduo, Bramble Board,<br>Steadyvolt Power</li>
  <li style="top:145px">Detailed build instructions, videos, walkthroughs</li>
  <li style="top:202px">DIY made to look professional</li>
</ul>
<a class="btn" href="#" style="left:620px;top:2155px">GET STARTED</a>

<svg class="band" style="top:2283px;height:569px" viewBox="0 0 1200 569" aria-hidden="true">
  <polygon points="0,0 1200,39 1200,569 0,530" fill="var(--mist)"/>
</svg>
<h2 class="centered-title" style="top:2394px">What our Customers Have to Say</h2>
<svg class="arrow" style="left:54px;top:2590px" viewBox="0 0 26 30"><path d="M18 3 L6 15 L18 27" stroke="#888" stroke-width="6" fill="none"/></svg>
<svg class="arrow" style="left:1118px;top:2590px" viewBox="0 0 26 30"><path d="M8 3 L20 15 L8 27" stroke="#888" stroke-width="6" fill="none"/></svg>
<article class="review" style="left:144px">
  <div class="avatar" role="img" aria-label="Customer avatar placeholder"></div>
  <div class="reviewer">Tomas R<small>Verified buyer</small></div>
  <p>Great work at a reasonable cost.<br>I can’t recommend them<br>enough.If you’re doing custom<br>boxes for light shows, this is<br>where you go.</p>
  <div class="quote-mark">”</div>
</article>
<article class="review" style="left:612px">
  <div class="avatar" role="img" aria-label="Customer avatar placeholder"></div>
  <div class="reviewer">Nils K.<small>Verified buyer</small></div>
  <p>Fantastic service/product..<br>whether you simply generate<br>the design and do all of the fab-<br>rication yourself or simply order<br>the kits.</p>
  <div class="quote-mark">”</div>
</article>

<h2 class="centered-title" style="top:2924px">See Real Examples from our Customers</h2>

<div class="tile" style="left:144px;top:2987px"><div class="shot green" role="img" aria-label="Customer build with stacked circuit boards"></div><div class="label">Ostbox32026_standalone_primary</div></div>
<div class="tile" style="left:451px;top:2987px"><div class="shot green" role="img" aria-label="Customer build with terminal blocks"></div><div class="label">Ostbox32022_standalone_primary</div></div>
<div class="tile" style="left:757px;top:2987px"><div class="shot dark" role="img" aria-label="Customer build on dark mounting plate"></div><div class="label">Ostbox32016_standalone_primary</div></div>

<div class="tile" style="left:144px;top:3251px"><div class="shot steel" role="img" aria-label="Customer build with power supply"></div><div class="label">Ostbox32012_standalone_primary</div></div>
<div class="tile" style="left:451px;top:3251px"><div class="shot steel" role="img" aria-label="Customer build with power supply"></div><div class="label">Ostbox32010_standalone_primary</div></div>
<div class="tile" style="left:757px;top:3251px"><div class="shot dark" role="img" aria-label="Customer build with wired boards"></div><div class="label">KP1500_standalone_primary</div></div>

<div class="tile" style="left:144px;top:3515px"><div class="shot tan" role="img" aria-label="Mounting plate with hardware bag"></div><div class="label">KP500_standalone_primary</div></div>
<div class="tile" style="left:451px;top:3515px"><div class="shot dark" role="img" aria-label="Customer build on dark tray"></div><div class="label">RTM30_standalone_primary</div></div>
<div class="tile" style="left:757px;top:3515px"><div class="shot green" role="img" aria-label="Customer build with two board layers"></div><div class="label">Lyn4_standalone_primary</div></div>

<a class="view-all" href="#">VIEW ALL</a>

<svg class="band" style="top:3905px;height:168px" viewBox="0 0 1200 168" aria-hidden="true">
  <polygon points="0,8 1200,0 1200,168 0,168" fill="var(--footer)"/>
</svg>
<nav class="footer-links">
  <a href="#">Get Started</a><span>|</span><a href="#">Designs</a><span>|</span><a href="#">FAQs</a><span>|</span><a href="#">Videos</a><span>|</span><a href="#">Contact Us</a>
</nav>
<div class="copyright">Copyright ©&nbsp; 2019 &nbsp;Vorelmik. &nbsp; All rights reserved.</div>
<div class="follow">Follow us :</div>
<div class="social" style="left:970px" aria-label="Social link"></div>
<div class="social" style="left:1018px" aria-label="Video channel link"></div>

</body>
</html>
```